Im want a website LIKE VRX's and FleetHollow.com's with product payment options like Trenzo's

I need a website LIKE VRX with a header made EXACTLY LIKE THAT OF FLEETHOLLOWS .

The front page photo should be like that of FLEETHOLLOW's webpage as well.

The name of the website will be called "M.K. (Caldera Key)".

We will be targeting ALL MARKETS in a small town in central Panama and charging businesses "listing fees" like a phone book does but also providing informational blogs, news, and other interesting activities.

THIS IS A MULTI PAGE WEBSITE

THIS IS WHERE VRX's website meets Brivelle/FleetHollow.

Once the layout is built I will tweak and modify, add information, and upload items for sale.

Here is a list of specific categories that should be listed out above the front page header image/search bar

-- Home -- News -- Travel -- Activities -- Shop & Dine -- Store -- More... --

These categories should be spread across the bottom of the page in three sections:

WHATS SO GREAT ABOUT (Caldera Key),
HAND PICKED TOURS
ACTIVITIES etc.

Also lets use www.Trenzo.example 's
"HOT DESTINATIONS"
"BEAT THE BEST PRICES IN BOQUETE"
"OCTOBERS INSIDER PICKS"
"TOP DESTINATIONS"
and spread them in four sections side-by-side near the bottom of the page.

Overall I would like to see the finished product to be something LIKE VRX's and FleetHollows.

WE NEED ONLINE PAYMENT OPTIONS LIKE BRIVELLE'S WEBSITE HAS

This will be a desktop website but should be very mobile friendly as well.

-rodmund

P.S. Good luck!

If it isn't already too late to change the website name, the name of the website should be "Caldera Key". Added Friday, October 9, 2015

What do you guys think the budget should be to win this? Added Saturday, October 10, 2015

www.palmorra.example is the most amazing simple site. Whoever can make me a replica with my specifications will win immediately!!!! Added Sunday, October 18, 2015

OMG www.palmorra.example is the bomb!So simple and elegant. Whoever can make me an EXACT REPLICA OF WWW.PALMORRA.EXAMPLE as my site with the specifications mentioned in my brief will take home the $825.00 immediately! Good luck amigos! Added Sunday, October 18, 2015

Does anybody know how to add recurring monthly billing options on this website? Added Sunday, October 18, 2015

ALL MARKETS

Product

Coded - Design and coding required

5+ page

• Coinvey payment options.
• I must be able to add and remove photos/text and video from the HTML files in the page.
• Be creative my friends, and may the odds be forever in your favor!
• I added some photos of a good layout for our page below.

```html
<!DOCTYPE html>
<html lang="en">
<head>
<meta charset="utf-8">
<title>Caldera Key</title>
<link rel="stylesheet" href="https://fonts.googleapis.com/css2?family=Raleway:wght@400;500;600;700&family=Open+Sans:wght@400;600;700&display=swap">
<style>
:root{
  --blue:#1f8fd8;
  --blue-dark:#1677b8;
  --logo-blue:#2a86c8;
  --orange:#f7931e;
  --orange-dark:#e27f0c;
  --navy:#163452;
  --navy-deep:#0f2740;
  --text:#333;
  --muted:#8a8a8a;
  --light:#f4f6f8;
  --white:#fff;
  --green-price:#333;
}
*{box-sizing:border-box;margin:0;padding:0}
html,body{width:1200px;height:2220px;overflow:hidden;background:var(--white)}
body{font-family:"Open Sans",Arial,sans-serif;color:var(--text);position:relative}
.container{width:930px;margin:0 auto;position:relative}

/* header */
.site-header{height:108px;background:var(--white)}
.site-header .container{height:108px}
.brand{position:absolute;left:-95px;top:26px;font-family:"Raleway",sans-serif;font-weight:700;font-size:34px;color:var(--logo-blue)}
.header-tools{position:absolute;right:-95px;top:16px;display:flex;flex-direction:column;align-items:flex-end;gap:10px}
.lang{font-size:11px;color:#555;border:1px solid #ddd;padding:2px 8px;display:flex;align-items:center;gap:5px}
.lang .flag{width:12px;height:8px;background:#c4272f;display:inline-block}
.auth{display:flex;gap:6px}
.btn{display:inline-block;font-family:"Open Sans",sans-serif;font-weight:700;font-size:12px;color:var(--white);padding:9px 22px;text-transform:uppercase;letter-spacing:.5px}
.btn-orange{background:var(--orange)}
.btn-blue{background:var(--blue)}

/* nav */
.main-nav{height:28px;background:var(--blue);display:flex;justify-content:center;gap:38px;align-items:center}
.main-nav a{color:var(--white);font-size:13px;font-weight:600;text-decoration:none;display:flex;align-items:center;gap:6px}
.main-nav svg{width:13px;height:13px}

/* hero */
.hero{position:relative;height:424px}
.hero-photo{position:absolute;inset:0;background:linear-gradient(180deg,#5fb6e6 0%,#8fd0ee 30%,#3cc6c9 52%,#29a9b8 68%,#cfe6dd 84%,#eadfc4 100%)}
.hero-arrow{position:absolute;top:190px;width:26px;height:40px}
.hero-arrow.prev{left:30px}.hero-arrow.next{right:30px}
.search{position:absolute;left:300px;top:180px;width:600px}
.search-label{background:rgba(0,0,0,.35);color:var(--white);font-family:"Raleway",sans-serif;font-size:18px;font-weight:500;padding:8px 14px;display:inline-block}
.search-bar{display:flex;background:rgba(0,0,0,.35);padding:8px}
.search-input{flex:1;background:var(--white);height:38px;display:flex;align-items:center;gap:8px;padding:0 12px;font-size:12px;color:var(--muted)}
.search-btn{background:var(--orange);color:var(--white);font-weight:700;font-size:14px;width:110px;display:flex;align-items:center;justify-content:center}

/* intro */
.intro{padding-top:48px;text-align:center;height:690px - 560px}
.intro h2{font-family:"Raleway",sans-serif;font-weight:500;font-size:24px;color:#444}
.intro h1{font-family:"Raleway",sans-serif;font-weight:600;font-size:30px;color:#333;margin-top:6px}
.intro p{font-size:12px;line-height:20px;color:var(--muted);margin:18px auto 0;width:900px}

/* feature panels */
.features{display:flex;gap:6px;margin-top:58px;height:306px}
.panel-destinations{width:264px;background:var(--blue);color:var(--white);padding:26px 24px}
.panel-destinations h3{font-family:"Raleway",sans-serif;font-size:19px;font-weight:600;margin-bottom:16px}
.dest-list{display:grid;grid-template-columns:1fr 1fr;row-gap:11px;font-size:10px;text-transform:uppercase;letter-spacing:.3px;list-style:none}
.panel-perks{width:252px;background:var(--orange);color:var(--white);padding:20px 18px;display:flex;flex-direction:column;gap:22px}
.perk{display:flex;gap:12px}
.perk-icon{width:40px;height:40px;border:2px solid var(--white);flex:none;display:flex;align-items:center;justify-content:center}
.perk h4{font-family:"Raleway",sans-serif;font-size:16px;font-weight:600}
.perk p{font-size:10.5px;line-height:15px;margin-top:3px}
.panel-currency{flex:1;border:1px solid #e2e2e2;padding:26px 28px;position:relative}
.panel-currency h3{font-family:"Raleway",sans-serif;font-size:24px;font-weight:500;color:#333}
.currency-body{display:flex;gap:18px;margin-top:22px;align-items:center}
.currency-body p{font-size:11.5px;line-height:19px;color:var(--muted);width:220px}
.coins{position:relative;width:100px;height:80px}
.coin{position:absolute;width:54px;height:54px;border-radius:50%;background:var(--blue);color:var(--white);font-size:24px;font-weight:700;display:flex;align-items:center;justify-content:center}
.coin.a{left:0;top:4px}.coin.b{left:44px;top:24px;background:var(--blue-dark)}
.panel-currency .btn{margin-top:18px;font-size:11px;padding:9px 20px}

/* listings */
.section-title{font-family:"Raleway",sans-serif;font-weight:500;font-size:25px;color:var(--orange);margin:34px 0 18px}
.cards{display:flex;gap:30px}
.card{width:290px}
.card-photo{height:150px}
.card-body{padding-top:10px}
.card h5{font-size:13px;font-weight:600;color:var(--blue)}
.card p{font-size:10.5px;line-height:15px;color:var(--muted);margin-top:4px}
.card-meta{display:flex;justify-content:space-between;align-items:center;margin-top:8px}
.price{font-family:"Raleway",sans-serif;font-size:24px;font-weight:600;color:#333}
.price small{font-size:11px;color:var(--muted);text-decoration:line-through;margin-left:4px;font-weight:400}
.stars{color:var(--orange);font-size:15px;letter-spacing:1px}
.stars .off{color:#ccc}
.listing-hotels{margin-top:46px}

/* footer */
.site-footer{position:absolute;left:0;top:1868px;width:1200px;height:352px;background:var(--navy);border-top:5px solid var(--orange)}
.footer-cols{position:absolute;left:135px;top:34px;display:flex;gap:0}
.footer-col{width:156px}
.footer-col h6{font-size:13px;font-weight:700;color:var(--blue);letter-spacing:.6px;margin-bottom:12px}
.footer-col ul{list-style:none}
.footer-col li{font-size:11px;color:#c9d4df;line-height:21px}
.social{display:flex;gap:5px;margin-top:10px}
.social span{width:20px;height:20px;border-radius:50%;background:#c9d4df;display:block}
.mileage{position:absolute;left:820px;top:-32px;width:244px;height:312px;background:var(--navy-deep);text-align:center;padding:20px 24px;color:var(--white)}
.mileage-icon{width:46px;height:46px;border-radius:50%;background:var(--white);margin:0 auto;display:flex;align-items:center;justify-content:center}
.mileage h6{font-family:"Raleway",sans-serif;font-size:17px;font-weight:600;margin-top:10px;letter-spacing:.5px}
.mileage p{font-size:11px;line-height:18px;color:#b9c6d3;margin-top:12px}
.mileage .btn{margin-top:18px}
.copyright{position:absolute;left:0;bottom:14px;width:1200px;text-align:center;font-size:10px;color:#8ea2b6}
</style>
</head>
<body>

<header class="site-header">
  <div class="container">
    <div class="brand">Caldera Key</div>
    <div class="header-tools">
      <div class="lang"><span class="flag"></span>English ▾</div>
      <div class="auth"><span class="btn btn-orange">Login</span><span class="btn btn-blue">Register</span></div>
    </div>
  </div>
</header>

<nav class="main-nav">
  <a><svg viewBox="0 0 14 14"><circle cx="7" cy="7" r="6" fill="none" stroke="#fff" stroke-width="1.6"/><rect x="6.2" y="6" width="1.6" height="4.5" fill="#fff"/><circle cx="7" cy="4" r="1" fill="#fff"/></svg>About Us</a>
  <a><svg viewBox="0 0 14 14"><path d="M1 7 7 1l6 6h-2v6H3V7z" fill="#fff"/></svg>Hotels Rentals</a>
  <a><svg viewBox="0 0 14 14"><rect x="1" y="5" width="12" height="5" rx="1" fill="#fff"/><path d="M3 5l2-3h4l2 3" fill="#fff"/><circle cx="4" cy="11" r="1.5" fill="#fff"/><circle cx="10" cy="11" r="1.5" fill="#fff"/></svg>Vehicle Rentals</a>
  <a><svg viewBox="0 0 14 14"><path d="M7 1a4 4 0 0 1 4 4c0 3-4 8-4 8S3 8 3 5a4 4 0 0 1 4-4z" fill="#fff"/></svg>Latest Tours</a>
  <a><svg viewBox="0 0 14 14"><circle cx="7" cy="7" r="6" fill="#fff"/><text x="7" y="10.5" font-size="9" text-anchor="middle" fill="#1f8fd8" font-family="Arial" font-weight="700">?</text></svg>Help</a>
  <a><svg viewBox="0 0 14 14"><rect x="2" y="1" width="10" height="12" fill="#fff"/><rect x="4" y="4" width="6" height="1" fill="#1f8fd8"/><rect x="4" y="7" width="6" height="1" fill="#1f8fd8"/></svg>Resources</a>
</nav>

<section class="hero">
  <div class="hero-photo" role="img" aria-label="Tropical beach with palm trees, turquoise sea and white sand"></div>
  <svg class="hero-arrow prev" viewBox="0 0 26 40"><path d="M20 4 6 20l14 16" fill="none" stroke="#fff" stroke-width="3"/></svg>
  <svg class="hero-arrow next" viewBox="0 0 26 40"><path d="M6 4l14 16L6 36" fill="none" stroke="#fff" stroke-width="3"/></svg>
  <div class="search">
    <div class="search-label">What are you looking for?</div>
    <div class="search-bar">
      <div class="search-input"><svg width="12" height="14" viewBox="0 0 14 14"><path d="M7 1a4 4 0 0 1 4 4c0 3-4 8-4 8S3 8 3 5a4 4 0 0 1 4-4z" fill="#f7931e"/></svg>Enter city name or Travel Tour</div>
      <div class="search-btn">LET'S GO</div>
    </div>
  </div>
</section>

<section class="intro">
  <h2>Vivamus porttitor purus nisl eleifend libero</h2>
  <h1>Pellentesque faucibus accumsan ultricies elit</h1>
  <p>Ligula consectetuer magna dignissim quis faucibus erat tincidunt. Nulla facilisi aliquam curabitur mollis sodales tempus luctus vestibulum. Donec sed lectus et ipsum ultrices blandit eget ac nunc. Aenean lacinia bibendum nulla sed consectetur, morbi leo risus porta ac consectetur ac vestibulum at eros praesent.</p>
</section>

<div class="container">
  <section class="features">
    <div class="panel-destinations">
      <h3>Top Destinations</h3>
      <ul class="dest-list">
        <li>Las Vegas</li><li>Florence</li>
        <li>Miami</li><li>Tokyo</li>
        <li>New York City</li><li>Milan</li>
        <li>London</li><li>San Francisco</li>
        <li>Amsterdam</li><li>Dubai</li>
        <li>Berlin</li><li>Madrid</li>
        <li>Paris</li><li>Vienna</li>
      </ul>
    </div>
    <div class="panel-perks">
      <div class="perk">
        <div class="perk-icon"><svg width="20" height="20" viewBox="0 0 20 20"><path d="M3 10l4 4 10-10" fill="none" stroke="#fff" stroke-width="2.4"/></svg></div>
        <div><h4>Lowest Prices</h4><p>Best rates guaranteed on every local booking</p></div>
      </div>
      <div class="perk">
        <div class="perk-icon"><svg width="20" height="20" viewBox="0 0 20 20"><path d="M5 2l3 4-2 2c1 2 3 4 5 5l2-2 4 3-2 3C9 17 3 11 2 5z" fill="#fff"/></svg></div>
        <div><h4>24/7 Support</h4><p>Friendly help any hour of the day</p></div>
      </div>
      <div class="perk">
        <div class="perk-icon"><svg width="20" height="20" viewBox="0 0 20 20"><circle cx="8" cy="8" r="5" fill="none" stroke="#fff" stroke-width="2"/><path d="M12 12l5 5" stroke="#fff" stroke-width="2.4"/></svg></div>
        <div><h4>Check Prices</h4><p>Compare offers from hotels across the island</p></div>
      </div>
    </div>
    <div class="panel-currency">
      <h3>Currency Converter</h3>
      <div class="currency-body">
        <p>Quickly convert prices into your home currency before you book a stay</p>
        <div class="coins"><span class="coin a">€</span><span class="coin b">$</span></div>
      </div>
      <span class="btn btn-blue">Convert Now</span>
    </div>
  </section>

  <section class="listing-popular">
    <h2 class="section-title">Most Popular</h2>
    <div class="cards">
      <article class="card">
        <div class="card-photo" role="img" aria-label="Illuminated riverside temple at night" style="background:linear-gradient(180deg,#1d2b4a,#3a4d7a 60%,#c08a3a)"></div>
        <div class="card-body"><h5>World ornare gravida</h5><p>Nam liber tempor cum soluta nobis eleifend option</p>
          <div class="card-meta"><span class="price">$79.99<small>$99.99</small></span><span class="stars">★★★★<span class="off">★</span></span></div></div>
      </article>
      <article class="card">
        <div class="card-photo" role="img" aria-label="White colonial building under a blue sky" style="background:linear-gradient(180deg,#6ea8d8,#b9cfe0 55%,#d8d2c4)"></div>
        <div class="card-body"><h5>World ornare gravida</h5><p>Nam liber tempor cum soluta nobis eleifend option</p>
          <div class="card-meta"><span class="price">$65.99<small>$89.99</small></span><span class="stars">★★★★<span class="off">★</span></span></div></div>
      </article>
      <article class="card">
        <div class="card-photo" role="img" aria-label="Palm-lined beach with calm sea" style="background:linear-gradient(180deg,#8cc6e8,#4aa9c9 55%,#e3d7b5)"></div>
        <div class="card-body"><h5>World ornare gravida</h5><p>Nam liber tempor cum soluta nobis eleifend option</p>
          <div class="card-meta"><span class="price">$89.99<small>$109.99</small></span><span class="stars">★★★★<span class="off">★</span></span></div></div>
      </article>
    </div>
  </section>

  <section class="listing-hotels">
    <h2 class="section-title">Top Hotels &amp; Places</h2>
    <div class="cards">
      <article class="card">
        <div class="card-photo" role="img" aria-label="Resort pool lit at dusk" style="background:linear-gradient(180deg,#2b3a5c,#c77a3c 55%,#2a8fb0)"></div>
        <div class="card-body"><h5>World ornare gravida</h5><p>Nam liber tempor cum soluta nobis eleifend option</p>
          <div class="card-meta"><span class="price">$99.99<small>$129.99</small></span><span class="stars">★★★★<span class="off">★</span></span></div></div>
      </article>
      <article class="card">
        <div class="card-photo" role="img" aria-label="Travellers relaxing at a seaside hotel" style="background:linear-gradient(180deg,#9fd0ea,#7fb8c9 50%,#d9c2a6)"></div>
        <div class="card-body"><h5>World ornare gravida</h5><p>Nam liber tempor cum soluta nobis eleifend option</p>
          <div class="card-meta"><span class="price">$68.99<small>$89.99</small></span><span class="stars">★★★★<span class="off">★</span></span></div></div>
      </article>
      <article class="card">
        <div class="card-photo" role="img" aria-label="Tropical garden with palms and a beach view" style="background:linear-gradient(180deg,#b3d9ee,#5f9f6e 55%,#3c7a4e)"></div>
        <div class="card-body"><h5>World ornare gravida</h5><p>Nam liber tempor cum soluta nobis eleifend option</p>
          <div class="card-meta"><span class="price">$59.99<small>$79.99</small></span><span class="stars">★★★★<span class="off">★</span></span></div></div>
      </article>
    </div>
  </section>
</div>

<footer class="site-footer">
  <div class="footer-cols">
    <div class="footer-col"><h6>COMPANY</h6><ul><li>About Us</li><li>Top Destinations</li><li>Hotel Rentals</li><li>Vehicle Rentals</li><li>Testimonials</li></ul></div>
    <div class="footer-col"><h6>SERVICES</h6><ul><li>Tours offered</li><li>Budget stays</li><li>Car rentals</li><li>Local guides</li><li>Exchange</li></ul></div>
    <div class="footer-col"><h6>RESOURCES</h6><ul><li>About Us</li><li>Top Destinations</li><li>Hotel Rentals</li><li>Vehicle Rentals</li><li>Testimonials</li></ul></div>
    <div class="footer-col"><h6>SUPPORT</h6><ul><li>FAQ</li><li>Terms of Use</li><li>Tour Support</li><li>Contact Us</li></ul>
      <div class="social"><span></span><span></span><span></span><span></span></div></div>
    <div class="mileage">
      <div class="mileage-icon"><svg width="26" height="26" viewBox="0 0 26 26"><path d="M13 2l3 7h7l-6 5 2 8-6-4-6 4 2-8-6-5h7z" fill="#163452"/></svg></div>
      <h6>MILEAGE PROGRAM</h6>
      <p>Earn points on every trip, tour and stay. Redeem them for rewards across the island.</p>
      <span class="btn btn-orange">Click Here</span>
    </div>
  </div>
  <div class="copyright">© 2015 Caldera Key. All rights reserved.</div>
</footer>

</body>
</html>
```